WordPress Website Design for Multi-Brand Aviation Group (Unified Branding System)

Project Overview:
We are seeking a professional, modern WordPress website design for an aviation-focused umbrella company that owns and operates multiple subsidiary businesses. The goal is to create a cohesive visual system that clearly communicates that each company operates under the same parent organization, while still allowing each brand to maintain a slightly distinct identity.
This is not just a single website design—we are looking for a scalable design framework that can be applied across multiple aviation-related businesses.
Objectives:
- Establish a consistent, recognizable brand identity across all company websites
Clearly communicate the relationship between the parent company and its subsidiaries
-bCreate a clean, high-end corporate aviation aesthetic
- Ensure all designs are SEO-friendly and optimized for performance
- Allow flexibility for future expansion (additional subsidiaries)
- Target Audience:
- Corporate aviation clients
- Charter customers
- Students wishing to receive flight training
- Aircraft owners and operators
- Turbine aircraft training to meet insurance requirements
- Business professionals and high-net-worth individuals
- Aviation industry partners
Design Direction & Style:
We are looking for a premium, professional aviation feel—think clean, modern, and high-trust. The design should reflect the standards of corporate aviation: precision, safety, and sophistication.
Key style notes:
Minimalist but impactful layout
High-quality aviation photography (jets, interiors, operations, global travel)
Subtle motion/interaction (hover effects, transitions)
Clear typography hierarchy for readability and professionalism
Branding Requirements:
Incorporate the primary colors of the parent company logo across all designs
Website Structure (Core Pages):
Design a system that includes:
Home Page with the following links:
- About / Company Overview
- Aircraft Management
- Aircraft Acquisition
- Charter
- Pilot Services
- Trip Support
- Contact Page
Site should further include:
- Mobile-first responsive design
- Fast-loading, performance-optimized layouts
SEO & Technical Considerations:
- Design should support high-level SEO implementation:
- Clean layout structure that translates well to semantic HTML
- Proper heading hierarchy (H1, H2, H3)
- Space for keyword-rich content without clutter
- Optimized image placement (with alt text capability)
- Fast load times (lightweight design approach)
- Compatibility with WordPress SEO plugins (e.g., Yoast or Rank Math)
WordPress Requirements:
- Design should be easily built using WordPress (preferred builders: Elementor, Gutenberg, or similar)
- Reusable templates for scalability across multiple sites
- Easy for non-developers to update text and images
- Modular components (blocks/sections that can be reused across pages and sites)
- Navigation & UX:
- Simple, intuitive navigation
- Sticky header preferred
Style guide including:
- Colors
- Fonts
- Button styles
- Layout system
- Designs similar to high-end corporate aviation, private jet charter, or luxury service brands are preferred—clean, sharp, and premium without being overly flashy.
What We Want to Avoid:
- Overly busy layouts
- Generic templates with no brand identity
- Outdated or “stock” looking aviation designs
- Poor mobile responsiveness
Additional Notes:
We are building a long-term brand system, not just a one-off website. There is potential for ongoing work as we expand additional subsidiary sites.
We value designers who understand branding consistency across multiple business units and can create a scalable, professional system.
Include the attached main company logo "Vireton Aviation Group" and the "Member PJFO" logo on the main page.

```html
<!DOCTYPE html>
<html lang="en">
<head>
<meta charset="utf-8">
<title>Vireton Aviation Group</title>
<link href="https://fonts.googleapis.com/css2?family=Audiowide&family=Roboto:wght@400;500;700&display=swap" rel="stylesheet">
<style>
:root{
  --blue:#0b5cb2;
  --blue-deep:#084a94;
  --ink:#111214;
  --text:#222;
  --muted:#6b6f75;
  --white:#fff;
  --footer:#0d0e11;
  --sky:#dbe9f6;
}
*{box-sizing:border-box;margin:0;padding:0}
html,body{width:1200px;height:3986px;overflow:hidden}
body{font-family:"Roboto",sans-serif;color:var(--text);background:var(--white)}
.page{position:relative;width:1200px;height:3986px;overflow:hidden}
.abs{position:absolute}
.display{font-family:"Audiowide",sans-serif;font-weight:400;text-transform:uppercase;line-height:1.3}
.btn{position:absolute;display:flex;align-items:center;justify-content:center;font-size:13px;font-weight:500;text-transform:uppercase;border-radius:3px;text-decoration:none}
.btn-blue{background:var(--blue);color:var(--white)}
.btn-white{background:var(--white);color:var(--blue)}
.btn-black{background:var(--ink);color:var(--white)}

/* header */
.topline{left:0;top:0;width:1200px;height:4px;background:var(--blue)}
.brand{left:144px;top:30px;display:flex;align-items:center;gap:12px}
.brand-dot{width:34px;height:34px;border-radius:50%;background:var(--blue)}
.brand-name{font-size:27px;font-weight:700;color:var(--blue);letter-spacing:.5px}
.call{left:604px;top:28px;display:flex;align-items:center;gap:14px}
.call-icon{width:38px;height:38px;border-radius:50%;background:var(--blue);display:flex;align-items:center;justify-content:center}
.call-label{font-size:15px;font-weight:500;color:var(--blue)}
.call-num{font-size:19px;color:var(--ink);margin-top:2px}
.head-btn{left:833px;top:26px;width:221px;height:44px}
.nav{left:0;top:99px;width:1200px;height:46px;background:var(--blue)}
.nav ul{position:absolute;left:136px;top:0;width:924px;height:46px;list-style:none;display:flex;justify-content:space-between;align-items:stretch}
.nav li{display:flex;align-items:center;color:var(--white);font-size:13.5px;font-weight:500;padding:0 4px}
.nav li.active{background:var(--ink);padding:0 14px}

/* hero */
.hero-photo{left:0;top:145px;width:1200px;height:730px;background:linear-gradient(180deg,#b9cee4 0%,#d6e4f1 40%,#e9f1f8 70%,#f6f9fc 100%)}
.hero-title{left:144px;top:540px;font-size:38px;line-height:53px;color:var(--blue)}
.hero-title .dark{color:var(--ink)}
.hero-text{left:736px;top:547px;width:318px;font-size:15.5px;line-height:26px;color:var(--text);text-align:justify}
.hero-btn{left:736px;top:704px;width:193px;height:43px}
.member{left:947px;top:711px;display:flex;align-items:center;gap:9px}
.member-dot{width:34px;height:34px;border-radius:50%;background:var(--blue)}
.member-name{font-size:20px;font-weight:500;color:var(--ink)}
.dots{left:1131px;top:577px}
.dots span{display:block;width:11px;height:11px;border-radius:50%;background:var(--white);margin-bottom:13px}
.dots span.on{background:var(--blue)}

/* about */
.snow{background:linear-gradient(180deg,rgba(255,255,255,0) 0%,#e2e8ef 45%,#c9d3de 70%,rgba(255,255,255,0) 100%)}
.about-block{left:144px;top:985px;width:232px;height:422px;background:var(--blue)}
.about-photo{left:195px;top:932px;width:418px;height:425px;background:linear-gradient(160deg,#8e9aa6 0%,#c9ced3 45%,#5f666d 100%)}
.section-title{font-size:40px;color:var(--blue)}
.about-title{left:671px;top:955px}
.lead{font-size:19px;line-height:30px;color:var(--ink);font-weight:400}
.about-lead{left:671px;top:1020px;width:400px}
.body-text{font-size:15px;line-height:27px;color:var(--muted);text-align:justify}
.about-text{left:671px;top:1093px;width:385px}
.about-btn{left:672px;top:1282px;width:139px;height:42px}

/* services split */
.split-title{font-size:40px;line-height:53px;color:var(--white)}
.split-sub{font-size:15.5px;line-height:25px;font-weight:700;color:var(--white)}
.split-body{font-size:15.5px;line-height:25px;color:var(--white)}
.mgmt-title{left:142px;top:1585px}
.mgmt-sub{left:144px;top:1700px;width:380px}
.mgmt-body{left:144px;top:1756px;width:380px}
.mgmt-btn{left:144px;top:1862px;width:139px;height:42px}
.acq-title{left:686px;top:1585px}
.acq-sub{left:688px;top:1700px;width:380px}
.acq-body{left:688px;top:1756px;width:380px}
.acq-btn{left:688px;top:1862px;width:139px;height:42px}

/* charters */
.charter-title{left:144px;top:2144px}
.charter-lead{left:145px;top:2215px;width:385px;font-size:17px;line-height:27px;font-weight:500}
.charter-text{left:145px;top:2268px;width:382px}
.charter-btn{left:146px;top:2487px;width:139px;height:42px}
.panel{top:2115px;height:425px}
.panel-a{left:598px;width:233px;background:linear-gradient(180deg,#0a4fa0 0%,#3d86cf 55%,#87b6de 100%);clip-path:polygon(0 5%,100% 0,100% 100%,0 100%)}
.panel-b{left:842px;width:232px;background:linear-gradient(180deg,#5e6166 0%,#9ea2a7 60%,#6c7075 100%)}
.panel-c{left:1085px;width:115px;background:linear-gradient(160deg,#0b55a8 0%,#2f7fcf 60%,#0a3f80 100%);clip-path:polygon(0 0,100% 3%,100% 100%,0 100%)}

/* pilot */
.pilot-title{left:664px;top:2795px}
.pilot-text{left:667px;top:2866px;width:380px}
.pilot-btn{left:667px;top:3110px;width:139px;height:42px}

/* trip */
.trip-title{left:175px;top:3318px;color:var(--white);font-size:40px}
.trip-sub{left:175px;top:3378px;font-size:19px;color:var(--white)}
.trip-text{left:656px;top:3323px;width:400px;font-size:17px;line-height:27px;color:var(--white)}
.trip-btn{left:657px;top:3395px;width:221px;height:43px}

/* footer */
.footer{left:0;top:3486px;width:1200px;height:500px;background:radial-gradient(ellipse at 75% 20%,#1d2229 0%,var(--footer) 60%)}
.foot-h{font-size:19px;font-weight:700;color:var(--white);text-transform:uppercase}
.contact-h{left:155px;top:3576px}
.touch-h{left:499px;top:3576px}
.c-row{left:156px;display:flex;align-items:center;gap:15px;color:var(--white)}
.c-icon{width:33px;height:33px;border-radius:50%;border:2px solid var(--white);display:flex;align-items:center;justify-content:center;flex:none}
.c-icon.fill{background:var(--blue);border-color:var(--blue)}
.c-row.addr{top:3643px;font-size:13.5px;line-height:22px}
.c-row.phone{top:3697px;font-size:18px;font-weight:500}
.c-row.mail{top:3750px;font-size:14px}
.socials{left:157px;top:3800px;display:flex;gap:7px}
.socials span{width:26px;height:26px;border-radius:50%;background:var(--blue);border:2px solid var(--white)}
.field{position:absolute;background:var(--white);border-radius:3px;font-size:12.5px;color:#888;padding:6px 12px}
.submit{left:500px;top:3834px;width:117px;height:28px;font-size:12.5px;font-weight:700}
.copy{left:0;top:3904px;width:1200px;text-align:center;font-size:14.5px;color:var(--white)}
</style>
</head>
<body>
<div class="page">

  <header>
    <div class="abs topline"></div>
    <div class="abs brand"><span class="brand-dot"></span><span class="brand-name">Vireton Aviation Group</span></div>
    <div class="abs call">
      <span class="call-icon"><svg width="18" height="18" viewBox="0 0 24 24"><path fill="#fff" d="M6.6 10.8a15.1 15.1 0 0 0 6.6 6.6l2.2-2.2a1 1 0 0 1 1-.25 11.4 11.4 0 0 0 3.6.57 1 1 0 0 1 1 1V20a1 1 0 0 1-1 1A17 17 0 0 1 3 4a1 1 0 0 1 1-1h3.5a1 1 0 0 1 1 1c0 1.25.2 2.45.57 3.57a1 1 0 0 1-.25 1z"/></svg></span>
      <div><div class="call-label">CALL US</div><div class="call-num">+1 888 888 8888</div></div>
    </div>
    <a class="btn btn-black head-btn">Request Consultation</a>
    <nav class="abs nav">
      <ul>
        <li class="active">HOME</li><li>ABOUT</li><li>AIRCRAFT MANAGEMENT</li><li>AIRCRAFT ACQUISITION</li><li>CHARTER</li><li>PILOT SERVICES</li><li>TRIP SUPPORT</li><li>CONTACT</li>
      </ul>
    </nav>
  </header>

  <section class="hero">
    <div class="abs hero-photo" role="img" aria-label="Passenger jet climbing above a sea of clouds under a bright sky"></div>
    <h1 class="abs display hero-title">Elevating Aviation<br><span class="dark">Ownership, Charter</span><br>&amp; Flight Solutions</h1>
    <p class="abs hero-text">Vireton Aviation Group delivers premium aviation services through a network of trusted subsidiaries specializing in aircraft management, charter, acquisitions, pilot services, and trip support.</p>
    <a class="btn btn-blue hero-btn">Explore Services</a>
    <div class="abs member"><span class="member-dot"></span><span class="member-name">Member PJFO</span></div>
    <div class="abs dots"><span class="on"></span><span></span><span></span></div>
    <svg class="abs" style="left:0;top:740px" width="1200" height="140" viewBox="0 0 1200 140">
      <polygon points="0,6 1040,105 1040,110 0,22" fill="#0b5cb2"/>
      <line x1="1105" y1="114" x2="1200" y2="126" stroke="#0b5cb2" stroke-width="1.5"/>
    </svg>
  </section>

  <section class="about">
    <div class="abs snow" style="left:0;top:1150px;width:1200px;height:360px" role="img" aria-label="Snow-covered mountain range fading into the page"></div>
    <div class="abs about-block"></div>
    <div class="abs about-photo" role="img" aria-label="Technician inspecting the landing gear and engine of a parked jet"></div>
    <h2 class="abs display section-title about-title">About Us</h2>
    <p class="abs lead about-lead">One Aviation Group.<br>Multiple Specialized Solutions.</p>
    <p class="abs body-text about-text">Vireton Aviation Group is a modern aviation holding company built to serve aircraft owners, charter clients, flight students, and aviation professionals through a unified network of specialized businesses. We combine operational excellence, safety, and premium service standards across every division.</p>
    <a class="btn btn-blue about-btn">Read More</a>
  </section>

  <section class="split">
    <svg class="abs" style="left:0;top:1420px" width="1200" height="650" viewBox="0 0 1200 650" role="img" aria-label="Engineer in a hard hat beside a jet engine, and a client reviewing documents in a cabin">
      <defs>
        <linearGradient id="mgmtTone" x1="0" y1="0" x2="1" y2="1"><stop offset="0" stop-color="#1a6fc4"/><stop offset=".6" stop-color="#0d5fb5"/><stop offset="1" stop-color="#084a94"/></linearGradient>
        <linearGradient id="acqTone" x1="0" y1="0" x2="1" y2="1"><stop offset="0" stop-color="#2b2c2f"/><stop offset=".6" stop-color="#3d3e41"/><stop offset="1" stop-color="#1c1d1f"/></linearGradient>
      </defs>
      <polygon points="0,20 595,150 595,546 0,644" fill="url(#mgmtTone)"/>
      <polygon points="600,150 1200,14 1200,644 600,546" fill="url(#acqTone)"/>
      <polygon points="598,142 1200,4 1200,12 598,150" fill="#111214"/>
    </svg>
    <h2 class="abs display split-title mgmt-title">Aircraft<br>Management</h2>
    <p class="abs split-sub mgmt-sub">Professional oversight, operations, maintenance coordination, and owner support.</p>
    <p class="abs split-body mgmt-body">Sed ut perspiciatis unde omnis iste natus error sit voluptatem accusantium doloremque laudantium, totam rem a inventore veritatis</p>
    <a class="btn btn-white mgmt-btn">Read More</a>
    <h2 class="abs display split-title acq-title">Aircraft<br>Acquisition</h2>
    <p class="abs split-sub acq-sub">Strategic sourcing, evaluations, negotiations, and seamless ownership transitions.</p>
    <p class="abs split-body acq-body">Sed ut perspiciatis unde omnis iste natus error sit voluptatem accusantium doloremque laudantium, totam rem a inventore veritatis</p>
    <a class="btn btn-blue acq-btn">Read More</a>
  </section>

  <section class="charters">
    <div class="abs snow" style="left:0;top:2380px;width:1200px;height:320px" role="img" aria-label="Snowy mountain peaks in soft grey tones"></div>
    <h2 class="abs display section-title charter-title">Our Charters</h2>
    <p class="abs lead charter-lead">Private charter solutions tailored for business and leisure travel.</p>
    <p class="abs body-text charter-text">Sed ut perspiciatis unde omnis iste natus error sit voluptatem accusantium doloremque laudantium, totam rem aperiam, eaque ipsa quae ab illo inventore veritatis et quasi architecto beatae vitae dicta sunt explicaboemo enim ipsam voluptatem quia voluptas sit aspernur aut odit a ipsa quae ab illo inventore veritatis et quasi architecto beatae</p>
    <a class="btn btn-blue charter-btn">Read More</a>
    <div class="abs panel panel-a" role="img" aria-label="Jet taking off with a second aircraft in the distance, blue tint"></div>
    <div class="abs panel panel-b" role="img" aria-label="Airliner lifting off above a runway, greyscale"></div>
    <div class="abs panel panel-c" role="img" aria-label="Close view of a jet engine intake, blue tint"></div>
  </section>

  <section class="pilot">
    <svg class="abs" style="left:0;top:2620px" width="1200" height="700" viewBox="0 0 1200 700">
      <defs>
        <linearGradient id="pilotSky" x1="0" y1="0" x2="1" y2="0"><stop offset="0" stop-color="#eef4fa"/><stop offset="1" stop-color="#d8e7f5"/></linearGradient>
        <linearGradient id="cockpit" x1="0" y1="0" x2="1" y2="1"><stop offset="0" stop-color="#6f7780"/><stop offset=".5" stop-color="#b7bcc2"/><stop offset="1" stop-color="#3b4148"/></linearGradient>
      </defs>
      <polygon points="0,95 1200,10 1200,700 0,700" fill="url(#pilotSky)"/>
      <polygon points="0,90 1200,5 1200,14 0,112" fill="#0b5cb2"/>
      <polygon points="0,110 655,65 655,605 0,570" fill="url(#cockpit)" role="img" aria-label="Two pilots seated in a cockpit, smiling toward the camera"/>
    </svg>
    <h2 class="abs display section-title pilot-title">Pilot Services</h2>
    <p class="abs body-text pilot-text">Sed ut perspiciatis unde omnis iste natus error sit voluptatem accusantium doloremque laudantium, totam rem aperiam, eaque ipsa quae ab illo inventore veritatis et quasi architecto beatae vitae dicta sunt explicabo. Nemo enim ipsam voluptatem quia voluptas sit aspernur aut odit aut fuged ut perspiciatis unde omnis iste natus error sit voluptatem accusantium doloremque laudantium</p>
    <a class="btn btn-blue pilot-btn">Read More</a>
  </section>

  <section class="trip">
    <svg class="abs" style="left:0;top:3180px" width="1200" height="310" viewBox="0 0 1200 310" role="img" aria-label="Jet on the apron under a deep blue overlay">
      <defs>
        <linearGradient id="tripTone" x1="0" y1="0" x2="1" y2="0"><stop offset="0" stop-color="#0d63bc"/><stop offset=".5" stop-color="#0b5cb2"/><stop offset="1" stop-color="#0a56a8"/></linearGradient>
      </defs>
      <polygon points="0,10 1200,115 1200,310 0,310" fill="url(#tripTone)"/>
      <polygon points="760,72 1200,108 1200,120 760,78" fill="#111214"/>
    </svg>
    <h2 class="abs display trip-title">Trip Support</h2>
    <p class="abs trip-sub">Ready to Elevate Your Aviation Experience?</p>
    <p class="abs trip-text">Speak with our team about ownership, charter, management, or training solutions.</p>
    <a class="btn btn-black trip-btn">Request Consultation</a>
  </section>

  <footer>
    <div class="abs footer"></div>
    <h3 class="abs foot-h contact-h">Contact Info</h3>
    <div class="abs c-row addr"><span class="c-icon"><svg width="14" height="16" viewBox="0 0 24 24"><path fill="#fff" d="M12 2a7 7 0 0 0-7 7c0 5 7 13 7 13s7-8 7-13a7 7 0 0 0-7-7zm0 9.5A2.5 2.5 0 1 1 12 6.5a2.5 2.5 0 0 1 0 5z"/></svg></span><span>123,Nemo enim ipsam volup<br>tatem quia voluptas sit</span></div>
    <div class="abs c-row phone"><span class="c-icon fill"><svg width="15" height="15" viewBox="0 0 24 24"><path fill="#fff" d="M6.6 10.8a15.1 15.1 0 0 0 6.6 6.6l2.2-2.2a1 1 0 0 1 1-.25 11.4 11.4 0 0 0 3.6.57 1 1 0 0 1 1 1V20a1 1 0 0 1-1 1A17 17 0 0 1 3 4a1 1 0 0 1 1-1h3.5a1 1 0 0 1 1 1c0 1.25.2 2.45.57 3.57a1 1 0 0 1-.25 1z"/></svg></span><span>Phone : +1 888 888 8888</span></div>
    <div class="abs c-row mail"><span class="c-icon"><svg width="15" height="12" viewBox="0 0 24 18"><path fill="#fff" d="M2 0h20a2 2 0 0 1 2 2v1l-12 7L0 3V2a2 2 0 0 1 2-2zm-2 6 12 7 12-7v10a2 2 0 0 1-2 2H2a2 2 0 0 1-2-2z"/></svg></span><span>info@companyname.com</span></div>
    <div class="abs socials" aria-label="Social links"><span></span><span></span><span></span><span></span></div>

    <h3 class="abs foot-h touch-h">Get In Touch</h3>
    <form>
      <div class="field" style="left:500px;top:3640px;width:268px;height:28px">Enter Name</div>
      <div class="field" style="left:777px;top:3640px;width:267px;height:28px">Enter Email</div>
      <div class="field" style="left:500px;top:3681px;width:268px;height:28px">Phone</div>
      <div class="field" style="left:777px;top:3681px;width:267px;height:28px">Zipcode</div>
      <div class="field" style="left:500px;top:3721px;width:544px;height:28px">Address</div>
      <div class="field" style="left:500px;top:3760px;width:544px;height:66px">Message</div>
      <a class="btn btn-blue submit">Submit</a>
    </form>
    <p class="abs copy">© 2026 Companyname.All Rights Reserved &nbsp;|&nbsp; Privacy Policy &nbsp;|&nbsp; Terms of use</p>
  </footer>

</div>
</body>
</html>
```